Business Card Design

I am after a business card design to be made for my pet care business in Darwin, Northern Territory Australia called Merry Tails. I am a certified canine trainer and offer training classes from puppy love class, basic obedience classes, intermediate classes, private lessons, mobile dog wash and grooming and pet minding. I currently have a logo that I would like used on the card that incorporates different shades of orange with the writing in black. I really want my card to stand out from the rest and look professional, easy to read with 'the edge' factor. Im thinking both sides printed on with contact details on one side and services provided on the back
Updates

Thank you all so much for your time. I am overwhelmed with designs as they are all 

really great. My business partner and myself have shortlisted a few that really caught our eye and
Will update as soon as we decide. 

Once again thank you to you all for your great designs :)

Reason: been very busy trying to decide

Industry/Entity Type

Training

Contact Information for Business Card

Merry Tails
merrytails@quikmailo.net
merrytails.com.au
0437206611
pet minding
Puppy classes
basic obedience classes
intermediate obedience classes
private lessons
mobile dog wash and grooming
certified dog trainer
CTGB certified
Police checked
fully insured
honest
reliable
find us on friendnest www.friendnest.com/merrytails

Requirements
Must have
• My current logo either the stacked version or side by side - whatever works best and must include my services

```html
<!DOCTYPE html>
<html lang="en">
<head>
<meta charset="utf-8">
<title>Merry Tails – Business Card</title>
<link rel="stylesheet" href="https://fonts.googleapis.com/css2?family=Dancing+Script:wght@500&family=Open+Sans:wght@700&family=Raleway:wght@300;400&display=swap">
<style>
  :root {
    --page: #ffffff;
    --card: #fdfdfd;
    --gold: #c8941a;
    --gold-mid: #dcae48;
    --gold-pale: #f1e2bd;
    --ink: #2b2b2b;
    --ink-soft: #3a3a3a;
    --rule: #3a3a3a;
    --social: #3b5b9a;
    --shadow: rgba(0, 0, 0, 0.16);
  }
  * { box-sizing: border-box; margin: 0; padding: 0; }
  html, body { width: 1012px; height: 1200px; overflow: hidden; }
  body { background: var(--page); position: relative; font-family: "Raleway", sans-serif; color: var(--ink); }

  .card {
    position: absolute;
    left: 111px;
    width: 799px;
    height: 470px;
    background: var(--card);
    border-radius: 40px;
    box-shadow: 0 6px 22px var(--shadow);
    overflow: hidden;
  }
  .card--front { top: 81px; }
  .card--back { top: 645px; }

  .mascot {
    position: absolute;
    border-radius: 46% 46% 18% 18%;
    background: linear-gradient(160deg, var(--gold) 0%, var(--gold-mid) 55%, var(--gold-pale) 100%);
  }
  .card--front .mascot { left: 141px; top: 47px; width: 134px; height: 146px; }
  .card--back .mascot { left: 32px; top: 158px; width: 204px; height: 220px; }

  .brand-rule {
    position: absolute;
    left: 301px; top: 34px;
    width: 1.5px; height: 166px;
    background: var(--rule);
  }

  .brand-name {
    position: absolute;
    left: 340px; top: 62px;
    font-family: "Raleway", sans-serif;
    font-weight: 300;
    font-size: 55px;
    line-height: 64px;
    letter-spacing: 3px;
    text-transform: uppercase;
    color: var(--ink);
  }

  .tagline {
    position: absolute;
    left: 0; right: 0; top: 196px;
    text-align: center;
    font-family: "Dancing Script", cursive;
    font-weight: 500;
    font-size: 50px;
    line-height: 60px;
    color: var(--ink);
  }

  .band {
    position: absolute;
    left: 0; right: 0;
    height: 40px;
    background: var(--gold);
    color: #fff;
    font-family: "Open Sans", sans-serif;
    font-weight: 700;
    text-align: center;
    line-height: 40px;
  }
  .card--front .band { top: 283px; font-size: 22px; }
  .card--back .band { top: 50px; font-size: 25px; }

  .contact { position: absolute; left: 197px; top: 344px; list-style: none; }
  .contact li {
    display: flex; align-items: center;
    height: 41px;
    font-size: 24px;
    color: var(--ink-soft);
  }
  .contact svg { width: 26px; height: 26px; margin-right: 14px; flex: none; }

  .services { position: absolute; left: 307px; top: 103px; list-style: none; }
  .services li {
    display: flex; align-items: center;
    height: 37.2px;
    font-size: 24px;
    color: var(--ink-soft);
  }
  .services li::before {
    content: "";
    width: 7px; height: 7px;
    border-radius: 50%;
    background: var(--gold);
    margin-right: 10px;
    flex: none;
  }

  .social {
    position: absolute; left: 263px; top: 406px;
    display: flex; align-items: center;
    height: 32px;
    font-size: 22px;
    color: var(--ink-soft);
  }
  .social-mark {
    width: 28px; height: 28px;
    border-radius: 4px;
    background: var(--social);
    margin-right: 13px;
  }
</style>
</head>
<body>

  <section class="card card--front" aria-label="Card front">
    <div class="mascot" role="img" aria-label="Logo illustration of pet silhouettes in shades of gold"></div>
    <div class="brand-rule" aria-hidden="true"></div>
    <h1 class="brand-name">Merry<br>Tails</h1>
    <p class="tagline">“Happy paws and merry tails”</p>
    <div class="band">www.merrytails.com.au</div>
    <ul class="contact">
      <li>
        <svg viewBox="0 0 24 24" aria-hidden="true"><path fill="#c8941a" d="M6.6 2.5c.6-.4 1.3-.3 1.7.3l2 3c.4.6.3 1.3-.2 1.8l-1.3 1.2c.9 2 2.6 3.8 4.6 4.8l1.3-1.3c.5-.5 1.2-.6 1.8-.2l3 2c.6.4.7 1.2.3 1.7l-1.6 2.1c-.6.8-1.6 1.1-2.6.8C9.7 17 5.3 12.4 3.6 6.7c-.3-1 0-2 .8-2.6z"/></svg>
        0437206611
      </li>
      <li>
        <svg viewBox="0 0 24 24" aria-hidden="true"><rect x="2.5" y="5.5" width="19" height="13" fill="none" stroke="#c8941a" stroke-width="1.5"/><path d="M2.5 5.5l9.5 7 9.5-7" fill="none" stroke="#c8941a" stroke-width="1.5"/></svg>
        merrytails@quikmailo.net
      </li>
    </ul>
  </section>

  <section class="card card--back" aria-label="Card back">
    <div class="band">Services provided:</div>
    <div class="mascot" role="img" aria-label="Logo illustration of pet silhouettes in shades of gold"></div>
    <ul class="services">
      <li>Pet minding</li>
      <li>Puppy classes</li>
      <li>Basic obedience classes</li>
      <li>Intermediate obedience classes</li>
      <li>Private lessons</li>
      <li>Mobile dog wash and grooming</li>
      <li>Certified dog trainer</li>
      <li>CTGB certified Police</li>
    </ul>
    <div class="social">
      <span class="social-mark" aria-hidden="true"></span>
      www.friendnest.com/merrytails
    </div>
  </section>

</body>
</html>
```